I would like a minimalist clean and uncluttered website design.
Initially, I would like to see a front page only and would then like to build on the project front there.
DVQ logo file with no background is attached, can be grey scale if the designer wishes.
I would like the front page to speak about the company's ethos and goals and I will need to put a great deal of thought into this to ensure it has the desired impact with the content on the subsequent pages.
The paragraph below gives a bit of an idea as to what this will include.
"DVQ is a technology company providing approachable IT products and services to business:
With the overwhelming advancements in technology, businesses often find it difficult to determine what is available and what best suits their businesses specific needs.
We can assist business with their IT infrustucture, devices, software in procurement, installation, training, cost control as well as ongoing administration and support. We also keep our Clients informed of new technology and products which can benefit them"
Target Market(s)
Business, Health, Education, Professional Practices. Target age would be around 30 plus either male or female. Office administration level through Managing Directors. English speaking.

```html
<!DOCTYPE html>
<html lang="en">
<head>
<meta charset="utf-8">
<title>DVQ – Home</title>
<link rel="stylesheet" href="https://fonts.googleapis.com/css2?family=Questrial&family=Open+Sans:ital,wght@0,300;0,400;1,300&display=swap">
<style>
  :root{
    --green:#8dbb4d;
    --blue:#34498a;
    --navy:#2b3c73;
    --text:#666;
    --nav:#555;
    --footer-bg:#f4f4f4;
    --line:#e6e6e6;
  }
  *{margin:0;padding:0;box-sizing:border-box}
  html,body{width:1200px;height:981px;overflow:hidden;background:#fff}
  body{position:relative;font-family:"Open Sans",sans-serif;color:var(--text)}
  .header{position:absolute;left:0;top:0;width:1200px;height:71px;background:#fff}
  .brand{position:absolute;left:178px;top:14px;display:flex;align-items:center;gap:8px}
  .brand-mark{width:28px;height:28px;background:var(--green)}
  .brand-name{font-family:"Questrial",sans-serif;font-size:24px;color:var(--blue);letter-spacing:3px}
  .brand-sub{position:absolute;left:178px;top:48px;font-family:"Questrial",sans-serif;font-size:12px;color:var(--nav);letter-spacing:1.5px}
  .nav a{position:absolute;top:26px;font-family:"Questrial",sans-serif;font-size:14px;color:var(--nav);text-decoration:none}
  .nav a.active{color:var(--green)}
  .nav-underline{position:absolute;left:477px;top:68px;width:83px;height:3px;background:var(--green)}
  .account{position:absolute;top:29px;font-size:10px;color:#999;display:flex;align-items:center;gap:3px}
  .account-sep{position:absolute;left:970px;top:29px;width:1px;height:12px;background:#ddd}

  .hero{position:absolute;left:0;top:71px;width:1200px;height:394px;
    background:linear-gradient(180deg,#3b3d40 0%,#5a5c60 35%,#4a4c50 70%,#2f3033 100%)}
  .hero-person{position:absolute;left:696px;top:0;width:354px;height:394px;
    background:linear-gradient(180deg,#3a3230 0%,#8e7f7a 40%,#d9d4e4 75%,#e7e3ee 100%);border-radius:140px 140px 0 0}
  .hero-title{position:absolute;left:173px;top:125px;font-family:"Questrial",sans-serif;font-size:29px;color:#fff}
  .hero-lead{position:absolute;left:173px;top:165px;font-size:16px;font-weight:300;font-style:italic;line-height:23px;color:#ddd}
  .btn{position:absolute;left:173px;top:235px;width:115px;height:31px;background:var(--green);color:#fff;
    font-family:"Open Sans",sans-serif;font-size:12.5px;line-height:31px;text-align:center;letter-spacing:-.3px}
  .dots{position:absolute;left:175px;top:341px;display:flex;gap:4px}
  .dots span{width:12.5px;height:12.5px;border-radius:50%;background:#fff}
  .dots span.on{box-shadow:inset 0 0 0 3px #fff;background:var(--blue)}

  .ribbon{position:absolute;left:437px;top:509px}
  .ribbon-label{position:absolute;left:31px;top:0;width:228px;height:38px;background:var(--blue);
    color:#fff;font-family:"Questrial",sans-serif;font-size:26px;line-height:40px;text-align:center}

  .service{position:absolute;width:230px}
  .service h3{display:flex;align-items:center;gap:10px;font-family:"Questrial",sans-serif;font-weight:400;font-size:17px;color:var(--blue);height:24px}
  .service h3 svg{flex:none}
  .service p{margin-top:9px;font-size:11px;line-height:14.5px;color:var(--text)}

  .footer{position:absolute;left:0;top:890px;width:1200px;height:91px;background:var(--footer-bg);border-top:1px solid var(--line)}
  .footer-links{position:absolute;left:171px;top:37px;font-size:10.5px;color:#666}
  .footer-links span.sep{margin:0 6px;color:#999}
  .social{position:absolute;left:946px;top:36px;display:flex;gap:4px}
  .social span{width:17px;height:17px;border-radius:50%;background:#555}
</style>
</head>
<body>
  <header class="header">
    <div class="brand"><span class="brand-mark"></span><span class="brand-name">DVQ</span></div>
    <div class="brand-sub">Davenquill</div>
    <nav class="nav">
      <a class="active" style="left:498px">Home</a>
      <a style="left:574px">Services</a>
      <a style="left:664px">Project</a>
      <a style="left:746px">Articles</a>
      <a style="left:830px">Contact</a>
    </nav>
    <div class="nav-underline"></div>
    <div class="account" style="left:920px">
      <svg width="8" height="9" viewBox="0 0 8 9"><rect x="0.5" y="4" width="7" height="5" fill="#aaa"/><path d="M2 4V2.5a2 2 0 0 1 4 0V4" fill="none" stroke="#aaa" stroke-width="1.2"/></svg>Log in</div>
    <div class="account-sep"></div>
    <div class="account" style="left:982px">
      <svg width="9" height="9" viewBox="0 0 9 9"><path d="M1 8l1-3 5-5 2 2-5 5z" fill="none" stroke="#aaa"/></svg>Sign up</div>
  </header>

  <section class="hero">
    <div class="hero-person" role="img" aria-label="Portrait photo of a smiling businesswoman in a white blouse"></div>
    <h1 class="hero-title">Welcome to DavenQuill</h1>
    <p class="hero-lead">DVQ is a technology company providing<br>approachable IT products and services to business.</p>
    <a class="btn">LEARN MORE</a>
    <div class="dots"><span></span><span class="on"></span><span></span><span></span></div>
  </section>

  <div class="ribbon">
    <svg width="290" height="49" viewBox="0 0 290 49">
      <polygon points="0,9 41,9 41,48 0,48 10,28" fill="var(--navy)"/>
      <polygon points="290,9 249,9 249,48 290,48 280,28" fill="var(--navy)"/>
      <polygon points="31,38 41,38 41,44" fill="#1d2a55"/>
      <polygon points="259,38 249,38 249,44" fill="#1d2a55"/>
    </svg>
    <div class="ribbon-label">OUR SERVICES</div>
  </div>

  <div class="service" style="left:173px;top:618px">
    <h3><svg width="23" height="21" viewBox="0 0 23 21"><rect x="1" y="1" width="21" height="14" fill="none" stroke="var(--blue)" stroke-width="2"/><rect x="9" y="15" width="5" height="3" fill="var(--blue)"/><rect x="6" y="18" width="11" height="2" fill="var(--blue)"/></svg>IT infrustucture</h3>
    <p>Lorem Ipsum is simply dummy text of the printing and typesetting industry. Lorem Ipsum dummy text ever since the 1500s...</p>
  </div>
  <div class="service" style="left:483px;top:618px">
    <h3><svg width="17" height="21" viewBox="0 0 17 21"><rect x="1" y="1" width="15" height="19" rx="1.5" fill="none" stroke="var(--blue)" stroke-width="2"/><circle cx="8.5" cy="17" r="1" fill="var(--blue)"/></svg>Devices</h3>
    <p>Lorem Ipsum is simply dummy text of the printing and typesetting industry. Lorem Ipsum dummy text ever since the 1500s...</p>
  </div>
  <div class="service" style="left:792px;top:618px">
    <h3><svg width="24" height="23" viewBox="0 0 24 23"><polygon points="12,1 23,6 12,11 1,6" fill="#4d63a5"/><polygon points="1,6 12,11 12,22 1,17" fill="var(--blue)"/><polygon points="23,6 12,11 12,22 23,17" fill="var(--navy)"/></svg>Software</h3>
    <p>Lorem Ipsum is simply dummy text of the printing and typesetting industry. Lorem Ipsum dummy text ever since the 1500s...</p>
  </div>
  <div class="service" style="left:173px;top:746px">
    <h3><svg width="17" height="23" viewBox="0 0 17 23"><rect x="0" y="0" width="17" height="2" fill="var(--blue)"/><rect x="0" y="21" width="17" height="2" fill="var(--blue)"/><path d="M2 2c0 6 6 7 6 9.5S2 15 2 21h13c0-6-6-7-6-9.5S15 8 15 2" fill="none" stroke="var(--blue)" stroke-width="1.6"/><polygon points="4,21 13,21 8.5,15" fill="var(--blue)"/></svg>Installation</h3>
    <p>Lorem Ipsum is simply dummy text of the printing and typesetting industry. Lorem Ipsum dummy text ever since the 1500s...</p>
  </div>
  <div class="service" style="left:483px;top:746px">
    <h3><svg width="21" height="22" viewBox="0 0 21 22"><path d="M5 21L2 12l-1-6 2 0 2 6V2h2v8V0h2v10V1h2v9V3h2v10l3-4 2 1-5 8-2 3z" fill="var(--blue)"/></svg>Training</h3>
    <p>Lorem Ipsum is simply dummy text of the printing and typesetting industry. Lorem Ipsum dummy text ever since the 1500s...</p>
  </div>
  <div class="service" style="left:792px;top:746px">
    <h3><svg width="33" height="21" viewBox="0 0 33 21"><rect x="5" y="1" width="27" height="15" fill="none" stroke="var(--blue)" stroke-width="1.5"/><rect x="3" y="3" width="27" height="15" fill="#fff" stroke="var(--blue)" stroke-width="1.5"/><rect x="1" y="5" width="27" height="15" fill="var(--blue)"/><rect x="4" y="8" width="21" height="9" fill="none" stroke="#fff" stroke-width="1"/><circle cx="14.5" cy="12.5" r="3.5" fill="#fff"/></svg>Cost cantrol</h3>
    <p>Lorem Ipsum is simply dummy text of the printing and typesetting industry. Lorem Ipsum dummy text ever since the 1500s...</p>
  </div>

  <footer class="footer">
    <div class="footer-links">Home<span class="sep">|</span>Services<span class="sep">|</span>Project<span class="sep">|</span>Articles<span class="sep">|</span>Contact<span class="sep">|</span>Copyright © 2013 DavenQuill.</div>
    <div class="social"><span></span><span></span><span></span><span></span></div>
  </footer>
</body>
</html>
```